Los Brava Dip – CPG Website with WordPress - Store Locator: WP Maps plugin

Larkfield Food Company is a startup consumer packaged goods (CPG) brand launching its flagship product line — Los Brava Dip. We’re seeking a talented web designer to create a bold, professional, mobile-optimized website using WordPress with a WP Maps store locator to help customers find local retailers.

Our goal is to build a strong online presence that supports both retail growth and direct-to-consumer sales.

See Los Brava _Website_Design_Brief word document.

The website URL is https://losbravadip.example/

Target Market(s)

Consumers of gourmet salsa

Industry/Entity Type

Consumer Packaged Goods - Salsa manufacturer.

Coding

Coded - Design and coding required

Number of Pages Required

5+ page

Requirements
Must have
• The design of the Los Brava Dip website shall emulate the clean, polished aesthetic of Fennigo.example.

```html
<!DOCTYPE html>
<html lang="en">
<head>
<meta charset="UTF-8">
<title>About Los Brava</title>
<link href="https://fonts.googleapis.com/css2?family=Oswald:wght@400;600;700&family=Poppins:wght@400;500;600&display=swap" rel="stylesheet">
<style>
:root{
  --red:#e0241b;
  --red-dark:#a3130d;
  --orange:#f2761d;
  --amber:#f8a12a;
  --ink:#1d1d1d;
  --text:#3b3b3b;
  --night:#141010;
  --card:#0d0b0b;
  --white:#ffffff;
  --gold:#f6b91c;
}
*{box-sizing:border-box;margin:0;padding:0}
html,body{width:683px;height:1200px;overflow:hidden}
body{font-family:"Poppins",Arial,sans-serif;color:var(--text);background:var(--white);position:relative}
.brand{font-family:"Oswald",Arial,sans-serif;font-weight:700;color:var(--red);text-transform:none;letter-spacing:.5px}

/* header */
.site-header{position:absolute;top:0;left:0;width:683px;height:38px;background:var(--white);display:flex;align-items:center;padding:0 22px;z-index:2}
.site-header .brand{font-size:22px}
.main-nav{display:flex;gap:22px;margin-left:auto;margin-right:20px}
.main-nav a{font-family:"Poppins",sans-serif;font-size:8px;font-weight:600;color:var(--ink);text-decoration:none;letter-spacing:.5px;padding-bottom:3px}
.main-nav a.active{border-bottom:2px solid var(--red)}
.btn-contact{background:var(--red);color:var(--white);font-size:8px;font-weight:600;padding:6px 14px;border-radius:14px;text-decoration:none;letter-spacing:.5px}

/* hero */
.hero{position:absolute;top:38px;left:0;width:683px;height:192px;background:radial-gradient(circle at 20% 30%,var(--amber),transparent 45%),radial-gradient(circle at 85% 20%,var(--red-dark),transparent 40%),linear-gradient(120deg,var(--orange),var(--red) 55%,var(--orange));display:flex;align-items:center;justify-content:center}
.hero h1{font-family:"Oswald",Arial,sans-serif;font-weight:700;font-size:42px;color:var(--white);letter-spacing:1px}

/* story */
.story{position:absolute;top:230px;left:0;width:683px;height:410px}
.story-photo{position:absolute;left:24px;top:58px;width:162px;height:162px;border-radius:50%;border:3px solid var(--red);padding:5px;background:var(--white)}
.story-photo div{width:100%;height:100%;border-radius:50%;background:radial-gradient(circle at 45% 40%,#d84a22,#8c2a14 55%,#3b2418)}
.story-copy{position:absolute;left:215px;top:30px;width:440px}
.eyebrow{font-size:8px;font-weight:600;color:var(--red);letter-spacing:1px}
.story-copy h2{font-family:"Oswald",Arial,sans-serif;font-weight:700;font-size:22px;color:var(--ink);margin-top:2px}
.underline{display:block;margin:2px 0 10px}
.story p,.story-wide{font-size:8.6px;line-height:13.5px;color:var(--text)}
.story-copy p+p{margin-top:11px}
.story-wide{position:absolute;left:24px;top:318px;width:635px}

/* reviews */
.reviews{position:absolute;top:640px;left:0;width:683px;height:280px;background:radial-gradient(circle at 15% 80%,#5a140d,transparent 40%),radial-gradient(circle at 90% 20%,#4a100a,transparent 40%),linear-gradient(180deg,#1b1412,var(--night));text-align:center;color:var(--white);overflow:hidden}
.reviews .eyebrow{color:var(--white);display:flex;align-items:center;justify-content:center;gap:8px;margin-top:30px}
.reviews .eyebrow::before,.reviews .eyebrow::after{content:"";width:30px;height:1px;background:var(--red)}
.reviews h2{font-family:"Oswald",Arial,sans-serif;font-weight:700;font-size:24px;margin-top:2px}
.rating{display:flex;align-items:center;justify-content:center;gap:6px;margin-top:8px;font-size:7px}
.stars{color:var(--gold);letter-spacing:2px;font-size:10px}
.review-row{position:absolute;top:120px;left:0;width:683px;height:100px}
.review-card{position:absolute;top:0;width:176px;height:98px;background:var(--card);border:1px solid #3a2a26;padding:10px 12px;text-align:left}
.review-card .stars{font-size:11px}
.review-card h3{font-size:9px;font-weight:600;margin:4px 0 3px}
.review-card p{font-size:6.6px;line-height:9.5px;color:#d4d4d4}
.review-card .author{font-size:7.5px;font-weight:600;color:var(--white);margin-top:5px}
.slider-nav{position:absolute;top:244px;left:0;width:683px;display:flex;justify-content:center;gap:22px}

/* follow */
.follow{position:absolute;top:920px;left:0;width:683px;height:150px;background:radial-gradient(circle at 20% 60%,var(--red-dark),transparent 40%),radial-gradient(circle at 80% 30%,var(--amber),transparent 45%),linear-gradient(110deg,var(--red),var(--orange));text-align:center}
.follow h2{font-family:"Oswald",Arial,sans-serif;font-weight:700;font-size:20px;color:var(--white);margin-top:30px;letter-spacing:.5px}
.follow h2::after{content:"";display:block;width:36px;height:2px;background:var(--white);margin:5px auto 0}
.social{display:flex;justify-content:center;gap:14px;margin-top:14px}
.social span{width:38px;height:38px;border-radius:50%;border:2px solid var(--white)}

/* footer */
.site-footer{position:absolute;top:1070px;left:0;width:683px;height:130px;background:var(--night);color:var(--white)}
.site-footer .brand{position:absolute;left:20px;top:40px;font-size:34px}
.footer-nav{position:absolute;left:200px;top:55px;display:flex;gap:16px}
.footer-nav a{font-size:7.5px;font-weight:500;color:var(--white);text-decoration:none;letter-spacing:.5px}
.footer-nav a+a::before{content:"•";margin-right:16px;color:var(--white)}
.footer-rule{position:absolute;left:200px;right:22px;top:78px;height:1px;background:#3a3232}
.copyright{position:absolute;left:200px;top:90px;font-size:6.5px;color:#c9c9c9}
.footer-meta{position:absolute;right:22px;top:86px;display:flex;align-items:center;gap:6px;font-size:6.5px;color:#c9c9c9}
.footer-meta .dot{width:12px;height:12px;border-radius:50%;background:var(--white)}
</style>
</head>
<body>

<header class="site-header">
  <span class="brand">Los Brava</span>
  <nav class="main-nav">
    <a class="active" href="#">ABOUT</a>
    <a href="#">PRODUCTS</a>
    <a href="#">WHERE TO BUY</a>
    <a href="#">RECIPES</a>
    <a href="#">REVIEW</a>
  </nav>
  <a class="btn-contact" href="#">CONTACT ›</a>
</header>

<section class="hero" role="img" aria-label="Bold orange and red abstract chili-inspired background">
  <h1>ABOUT LOS BRAVA</h1>
</section>

<section class="story">
  <div class="story-photo"><div role="img" aria-label="Photo of red chili peppers in a rustic bowl"></div></div>
  <div class="story-copy">
    <p class="eyebrow">OUR STORY</p>
    <h2>ABOUT LOS BRAVA</h2>
    <svg class="underline" width="70" height="6" viewBox="0 0 70 6"><path d="M2 4 Q35 0 68 3" stroke="#e0241b" stroke-width="2.5" fill="none" stroke-linecap="round"/></svg>
    <p>Los Brava was founded in 2025 with a simple vision: to create bold, premium salsas that deliver authentic flavor using real, honest ingredients. What began as a homegrown recipe has grown into a professionally scaled brand, built for regional retail distribution and future expansion.</p>
    <p>Crafted in small batches using vine-ripened crushed tomatoes, real chili pepper purées, and carefully balanced natural spices, each Los Brava variety offers rich texture and depth—without fillers, preservatives, or shortcuts. From the classic All Natural to the Habanero, every jar reflects a commitment to quality and flavor integrity.</p>
  </div>
  <p class="story-wide">With production based in Texas, Los Brava partners with local suppliers, regional co-packers, and independent retailers to ensure consistency, freshness, and operational scalability. The company is driven by a belief that great food is rooted in simplicity, and that authenticity always earns shelf space.</p>
</section>

<section class="reviews" role="img" aria-label="Dark background of scattered red chili peppers">
  <p class="eyebrow">WHAT PEOPLE SAYS</p>
  <h2>CUSTOMER REVIEWS</h2>
  <div class="rating"><span class="stars">★★★★★</span><span>4.8 From 485 Reviews</span></div>
  <div class="review-row">
    <article class="review-card" style="left:-150px"><div class="stars">★★★★★</div><h3>Awesome taste, fresh</h3><p>Rich and tangy with real depth.</p></article>
    <article class="review-card" style="left:56px"><div class="stars">★★★★★</div><h3>Awesome taste, fresh</h3><p>Bright, smoky flavor with just enough heat. Our whole family keeps asking for more jars.</p><p class="author">Sam Ortiz</p></article>
    <article class="review-card" style="left:253px"><div class="stars">★★★★★</div><h3>Awesome taste, fresh</h3><p>Bright, smoky flavor with just enough heat. Our whole family keeps asking for more jars.</p><p class="author">Sam Ortiz</p></article>
    <article class="review-card" style="left:450px"><div class="stars">★★★★★</div><h3>Awesome taste, fresh</h3><p>Bright, smoky flavor with just enough heat. Our whole family keeps asking for more jars.</p><p class="author">Sam Ortiz</p></article>
    <article class="review-card" style="left:656px"><div class="stars">★★★★★</div><h3>Awesome</h3></article>
  </div>
  <div class="slider-nav">
    <svg width="12" height="16" viewBox="0 0 12 16"><path d="M9 2 L3 8 L9 14" stroke="#fff" stroke-width="2" fill="none"/></svg>
    <svg width="12" height="16" viewBox="0 0 12 16"><path d="M3 2 L9 8 L3 14" stroke="#fff" stroke-width="2" fill="none"/></svg>
  </div>
</section>

<section class="follow" role="img" aria-label="Orange and red abstract background">
  <h2>FOLLOW US ON</h2>
  <div class="social"><span></span><span></span></div>
</section>

<footer class="site-footer">
  <span class="brand">Los Brava</span>
  <nav class="footer-nav">
    <a href="#">ABOUT</a><a href="#">PRODUCTS</a><a href="#">WHERE TO BUY</a><a href="#">RECIPES</a><a href="#">REVIEW</a><a href="#">CONTACT</a>
  </nav>
  <div class="footer-rule"></div>
  <p class="copyright">© 2025 Los Brava All rights reserved</p>
  <div class="footer-meta"><span class="dot"></span><span class="dot"></span><span>Privacy Policy</span><span>Terms of Use</span></div>
</footer>

</body>
</html>
```